Poster/Handout for a dance

I need a poster designed that can also be made into a hand bill. Id like it to have an elegant feel - maybe black and gold

Wording: (feel free to tweak it)

Chairman's Soirée
All adults and invited guests Join us for some R&R
an evening of music, dancing, relaxation, and appetizers and desserts
Friday, February 24 2017
8PM-11PM
North Vale Hall
4821 Maplebrook Cres NW

some ideas of looks below....

Font styles to use
Serif
Script

Colors
757575
000000

Requirements
Must have
• elegance....impact...professionalism
Should not have
• not too casual

```html
<!DOCTYPE html>
<html lang="en">
<head>
<meta charset="utf-8">
<title>Chairman's Soirée – R&amp;R Evening</title>
<link href="https://fonts.googleapis.com/css2?family=Roboto+Condensed:wght@300;400&family=Roboto:wght@400&family=Great+Vibes&display=swap" rel="stylesheet">
<style>
  :root{
    --stage:#e4e4e4;
    --ink:#000000;
    --gold:#e8c873;
    --gold-light:#fff3c4;
    --gold-deep:#a87a1e;
    --cream:#fff6d2;
    --white:#ffffff;
  }
  html,body{margin:0;padding:0;width:1200px;height:1200px;overflow:hidden;background:var(--stage);}
  .poster{
    position:absolute;left:167px;top:40px;width:866px;height:1120px;
    background:var(--ink);overflow:hidden;
    font-family:"Roboto Condensed",Arial,sans-serif;color:var(--cream);
  }
  .sparkle-field{
    position:absolute;left:0;top:0;width:866px;height:470px;
    background:
      radial-gradient(ellipse 55% 60% at 50% 0%, rgba(255,236,170,.75), rgba(214,160,50,.35) 45%, rgba(0,0,0,0) 75%),
      radial-gradient(ellipse 40% 50% at 10% 20%, rgba(220,170,60,.35), rgba(0,0,0,0) 70%),
      radial-gradient(ellipse 40% 50% at 90% 20%, rgba(220,170,60,.35), rgba(0,0,0,0) 70%),
      linear-gradient(180deg, #3a2a0c 0%, #1a1206 55%, var(--ink) 100%);
  }
  .crest{
    position:absolute;left:300px;top:20px;width:266px;height:266px;border-radius:50%;
    box-sizing:border-box;border:7px solid var(--gold);background:var(--ink);
    box-shadow:0 0 0 3px var(--gold-deep), 0 0 30px rgba(255,220,140,.6);
  }
  .crest-title{
    position:absolute;left:0;right:0;top:66px;text-align:center;
    font-size:33px;color:var(--gold-light);line-height:1;
  }
  .crest-script{
    position:absolute;left:0;right:0;top:108px;text-align:center;
    font-family:"Great Vibes",cursive;font-size:62px;color:var(--gold-light);line-height:1;
  }
  .invite{
    position:absolute;left:0;right:0;top:448px;text-align:center;
    font-size:34px;line-height:46px;color:var(--white);text-transform:uppercase;
  }
  .headline{
    position:absolute;left:0;right:0;top:535px;text-align:center;
    font-family:"Roboto",Arial,sans-serif;font-size:168px;line-height:1;letter-spacing:-2px;
    background:linear-gradient(180deg,#fffbe8 0%,var(--gold-light) 40%,#c9a45a 70%,#fff0c0 100%);
    -webkit-background-clip:text;background-clip:text;color:transparent;
  }
  .glow-rule{
    position:absolute;left:200px;width:466px;height:2px;
    background:linear-gradient(90deg,rgba(0,0,0,0),var(--gold-light),rgba(0,0,0,0));
    box-shadow:0 0 12px rgba(255,220,140,.8);
  }
  .glow-rule.under-headline{top:690px;}
  .glow-rule.wide{left:40px;width:786px;}
  .glow-rule.top-band{top:952px;}
  .glow-rule.bottom-band{top:1076px;}
  .offer{
    position:absolute;left:0;right:0;top:708px;text-align:center;
    font-size:31px;line-height:44px;color:var(--cream);
  }
  .activity-icons{position:absolute;left:0;top:806px;width:866px;height:106px;}
  .activity-icons .badge{
    position:absolute;top:0;width:106px;height:106px;border-radius:50%;
    background:radial-gradient(circle at 40% 35%,#fffdf0 0%,var(--gold-light) 55%,#c9a45a 100%);
  }
  .date{
    position:absolute;left:0;right:0;top:955px;text-align:center;
    font-weight:300;font-size:68px;line-height:1;color:var(--cream);
  }
  .details{
    position:absolute;left:71px;right:40px;top:1028px;display:flex;align-items:center;
    color:var(--cream);white-space:nowrap;
  }
  .details .time{font-size:34px;}
  .details .divider{font-size:30px;margin:0 26px;}
  .details .venue{font-size:23px;text-transform:uppercase;}
</style>
</head>
<body>
  <div class="poster">
    <div class="sparkle-field" role="img" aria-label="Gold glitter and falling stars with light rays"></div>
    <div class="crest">
      <div class="crest-title">Chairman's</div>
      <div class="crest-script">Soirée</div>
    </div>

    <div class="invite">All adults and invited guests<br>join us for some</div>
    <div class="headline">R&amp;R</div>
    <div class="glow-rule under-headline"></div>

    <div class="offer">An evening of<br>Music, Dancing, Relaxation, Appetizers and Desserts</div>

    <div class="activity-icons">
      <div class="badge" style="left:158px" role="img" aria-label="Music note icon"></div>
      <div class="badge" style="left:269px" role="img" aria-label="Dancer silhouette icon"></div>
      <div class="badge" style="left:377px" role="img" aria-label="Relaxation figure icon"></div>
      <div class="badge" style="left:486px" role="img" aria-label="Plate with spoon and fork icon"></div>
      <div class="badge" style="left:595px" role="img" aria-label="Cupcake icon"></div>
    </div>

    <div class="glow-rule wide top-band"></div>
    <div class="date">FRIDAY, FEBRUARY 24 2017</div>
    <div class="details">
      <span class="time">8PM-11PM</span>
      <span class="divider">|</span>
      <span class="venue">North Vale Hall 4821 Maplebrook Cres NW</span>
    </div>
    <div class="glow-rule wide bottom-band"></div>
  </div>
</body>
</html>
```